Brightwave Reach - Business Card

We need a business card for a Social Media Marketing company that specializes in online marketing for small businesses in Canada using common Social Media platforms such as Pixlora, Chatterly, Blinkpost & Quibber.

I have uploaded a copy of our logo which I would like utilized in the business card. We would like the business card to be modern yet classy design.

Our website is www.brightwavereach.ca

Industry/Entity Type

Marketing

Contact Information for Business Card

Email: info@brightwavereach.ca
Website: www.brightwavereach.ca
Telephone: 604-555-0193

Colors

Designer to choose colors to be used in the design.

Requirements
Must have
• Social Media icons on reverse
• Please add some designs with color.

```html
<!DOCTYPE html>
<html lang="en">
<head>
<meta charset="utf-8">
<title>Brightwave Reach – Business Card</title>
<link rel="stylesheet" href="https://fonts.googleapis.com/css2?family=Lato:wght@400;700;900&display=swap">
<style>
  :root {
    --backdrop: #e4e4e2;
    --paper: #ffffff;
    --slate: #3c4043;
    --ink: #2b2b2b;
    --ink-soft: #4a4a4a;
    --accent: #d2692a;
  }
  * { box-sizing: border-box; margin: 0; padding: 0; }
  html, body { width: 1200px; height: 800px; overflow: hidden; }
  body {
    background: var(--backdrop);
    font-family: "Lato", Arial, sans-serif;
    position: relative;
  }
  .card {
    position: absolute;
    left: 300px;
    width: 600px;
    height: 343px;
    overflow: hidden;
    box-shadow: 0 6px 18px rgba(0,0,0,.18);
  }
  .card--back { top: 30px; background: var(--slate); }
  .card--front { top: 410px; background: var(--paper); }
  .card--front::after, .card--back::after {
    content: ""; position: absolute; left: 0; right: 0; bottom: 0; height: 7px;
    background: var(--accent);
  }

  /* wordmark */
  .wordmark {
    display: flex; align-items: center; gap: 12px;
    font-weight: 900; text-transform: uppercase; letter-spacing: 1px;
    line-height: 1.05;
  }
  .wordmark__square { width: 22px; height: 22px; flex: none; }
  .wordmark__name { font-size: 30px; }

  /* back */
  .card--back .wordmark {
    position: absolute; top: 70px; left: 0; right: 0; justify-content: center;
    color: var(--paper);
  }
  .card--back .wordmark__square { background: var(--accent); }
  .social-row {
    position: absolute; top: 205px; left: 0; right: 0;
    display: flex; justify-content: center; gap: 54px;
  }
  .social {
    display: flex; flex-direction: column; align-items: center; gap: 10px;
    color: var(--paper); font-size: 13px; font-weight: 700; letter-spacing: .5px;
  }
  .social__tile {
    width: 40px; height: 40px; border-radius: 6px; background: var(--paper);
    display: flex; align-items: center; justify-content: center;
  }
  .social__tile span { width: 22px; height: 22px; border-radius: 4px; background: var(--accent); }

  /* front */
  .card--front .wordmark {
    position: absolute; top: 138px; left: 40px; width: 215px; color: var(--slate);
  }
  .card--front .wordmark__name { font-size: 24px; }
  .card--front .wordmark__square { border: 3px solid var(--slate); }
  .divider {
    position: absolute; left: 278px; top: 98px; width: 2px; height: 130px;
    background: var(--accent);
  }
  .person { position: absolute; left: 318px; top: 108px; }
  .person__name { color: var(--accent); font-size: 26px; font-weight: 700; }
  .person__role { color: var(--ink-soft); font-size: 17px; margin-top: 2px; }
  .contact { list-style: none; margin-top: 20px; }
  .contact li {
    display: flex; align-items: center; gap: 12px;
    color: var(--ink); font-size: 18px; line-height: 26px;
  }
  .contact svg { width: 14px; height: 14px; flex: none; fill: var(--accent); }
</style>
</head>
<body>

<section class="card card--back" aria-label="Card reverse">
  <div class="wordmark">
    <span class="wordmark__square"></span>
    <span class="wordmark__name">Brightwave Reach</span>
  </div>
  <div class="social-row">
    <div class="social"><div class="social__tile"><span></span></div>Chatterly</div>
    <div class="social"><div class="social__tile"><span></span></div>Pixlora</div>
    <div class="social"><div class="social__tile"><span></span></div>Quibber</div>
    <div class="social"><div class="social__tile"><span></span></div>Blinkpost</div>
  </div>
</section>

<section class="card card--front" aria-label="Card front">
  <div class="wordmark">
    <span class="wordmark__square"></span>
    <span class="wordmark__name">Brightwave Reach</span>
  </div>
  <div class="divider"></div>
  <div class="person">
    <p class="person__name">Daniel Mercer</p>
    <p class="person__role">Manager</p>
    <ul class="contact">
      <li>
        <svg viewBox="0 0 24 24" aria-hidden="true"><path d="M6.6 10.8a15.1 15.1 0 0 0 6.6 6.6l2.2-2.2c.3-.3.7-.4 1-.2 1.1.4 2.3.6 3.6.6.6 0 1 .4 1 1V20c0 .6-.4 1-1 1C10.6 21 3 13.4 3 4c0-.6.4-1 1-1h3.5c.6 0 1 .4 1 1 0 1.3.2 2.5.6 3.6.1.3 0 .7-.2 1z"/></svg>
        604-555-0193
      </li>
      <li>
        <svg viewBox="0 0 24 24" aria-hidden="true"><path d="M2 5h20v14H2zM4 7v.5l8 5 8-5V7l-8 5z"/></svg>
        info@brightwavereach.ca
      </li>
      <li>
        <svg viewBox="0 0 24 24" aria-hidden="true"><path d="M12 2a10 10 0 1 0 0 20 10 10 0 0 0 0-20zm6.9 6h-3a15 15 0 0 0-1.3-3.9A8 8 0 0 1 18.9 8zM12 4c.8 1.2 1.5 2.5 1.9 4h-3.8c.4-1.5 1.1-2.8 1.9-4zM4.3 14a8 8 0 0 1 0-4h3.4a16 16 0 0 0 0 4zm.8 2h3a15 15 0 0 0 1.3 3.9A8 8 0 0 1 5.1 16zm3-8h-3a8 8 0 0 1 4.3-3.9A15 15 0 0 0 8.1 8zM12 20c-.8-1.2-1.5-2.5-1.9-4h3.8c-.4 1.5-1.1 2.8-1.9 4zm2.3-6H9.7a14 14 0 0 1 0-4h4.6a14 14 0 0 1 0 4zm.3 5.9a15 15 0 0 0 1.3-3.9h3a8 8 0 0 1-4.3 3.9zm1.7-5.9a16 16 0 0 0 0-4h3.4a8 8 0 0 1 0 4z"/></svg>
        www.brightwavereach.ca
      </li>
    </ul>
  </div>
</section>

</body>
</html>
```